New business card/stationary for a consulting company

I am looking for a clean and very professional looking business card for my consulting company as well as corresponding stationary. I am uploading our logo. I like simple and powerful for the feel. No graphics but I am open on everything else. Below is my contact information but would like the final to be in a version I can add my employees information into and print. Thank you.

Daniel Whitcombe
dan@ferncliffadvisory.com
2870 North 9th Avenue, Summit Floor, Elm Ridge, Illinois 60531
www.ferncliffadvisory.com

Industry/Entity Type

Consulting

Contact Information for Business Card

Daniel Whitcombe
dan@ferncliffadvisory.com
www.ferncliffadvisory.com

Font styles to use
Serif
Sans Serif

Requirements
Must have
• Our logo and the business card details.
Nice to have
• our website www.ferncliffadvisory.com

```html
<!DOCTYPE html>
<html lang="en">
<head>
<meta charset="utf-8">
<title>Ferncliff Advisory — Business Card</title>
<link rel="stylesheet" href="https://fonts.googleapis.com/css2?family=EB+Garamond:wght@400;600;700&family=Questrial&display=swap">
<style>
  :root {
    --navy: #0b0b9c;
    --navy-deep: #05057a;
    --paper: #ffffff;
    --ink: #1b1b2e;
    --backdrop: #e9e9ec;
    --rule-light: #e6e6f2;
  }
  * { box-sizing: border-box; margin: 0; padding: 0; }
  html, body {
    width: 1200px; height: 900px; overflow: hidden;
    background: var(--backdrop);
  }
  .canvas {
    position: relative; width: 1200px; height: 900px;
    display: flex; flex-direction: column; align-items: center;
    justify-content: center; gap: 34px;
  }
  .card {
    position: relative; width: 700px; height: 400px; overflow: hidden;
    box-shadow: 0 6px 18px rgba(0,0,0,.18);
  }

  /* Front */
  .card--front {
    background: radial-gradient(ellipse at 40% 30%, var(--navy) 0%, var(--navy-deep) 100%);
    color: var(--paper);
  }
  .front-brand {
    position: absolute; left: 0; right: 0; top: 120px;
    display: flex; align-items: center; justify-content: center; gap: 18px;
  }
  .brand-square {
    width: 34px; height: 34px; background: currentColor;
  }
  .brand-name {
    font-family: "Questrial", sans-serif;
    font-size: 40px; letter-spacing: 2px; line-height: 1; white-space: nowrap;
  }
  .front-rule {
    position: absolute; height: 2px; background: var(--rule-light);
  }
  .front-rule--upper { right: 0; width: 200px; top: 208px; }
  .front-rule--lower { left: 0; width: 220px; top: 320px; }
  .front-url {
    position: absolute; left: 0; right: 0; top: 236px; text-align: center;
    font-family: "EB Garamond", serif; font-size: 21px; letter-spacing: .3px;
  }

  /* Back */
  .card--back { background: var(--paper); color: var(--navy); }
  .back-brand {
    position: absolute; left: 90px; top: 92px;
    display: flex; align-items: center; gap: 14px;
  }
  .back-brand .brand-name { font-size: 34px; }
  .back-brand .brand-square { width: 28px; height: 28px; }
  .divider {
    position: absolute; left: 0; top: 222px; width: 425px; height: 1.5px;
    background: var(--ink);
  }
  .holder-name {
    position: absolute; left: 430px; top: 196px;
    font-family: "EB Garamond", serif; font-weight: 700;
    font-size: 25px; letter-spacing: .4px; text-transform: uppercase;
    white-space: nowrap;
  }
  .address {
    position: absolute; left: 432px; top: 236px;
    display: flex; gap: 12px; align-items: flex-start;
    font-family: "EB Garamond", serif; color: var(--ink);
    font-size: 16px; line-height: 1.35;
  }
  .contact-list {
    position: absolute; left: 150px; top: 262px; list-style: none;
    font-family: "EB Garamond", serif; color: var(--ink); font-size: 18px;
  }
  .contact-list li {
    display: flex; align-items: center; gap: 12px; margin-bottom: 8px;
  }
  .icon-box {
    width: 24px; height: 24px; background: var(--navy);
    display: inline-flex; align-items: center; justify-content: center; flex: none;
  }
  .band {
    position: absolute; left: 0; right: 0; bottom: 0; height: 30px;
    background: var(--navy);
  }
</style>
</head>
<body>
<main class="canvas">

  <section class="card card--front" aria-label="Card front">
    <div class="front-brand">
      <span class="brand-square" aria-hidden="true"></span>
      <span class="brand-name">FERNCLIFF ADVISORY</span>
    </div>
    <div class="front-rule front-rule--upper"></div>
    <p class="front-url">www.ferncliffadvisory.com</p>
    <div class="front-rule front-rule--lower"></div>
  </section>

  <section class="card card--back" aria-label="Card back">
    <div class="back-brand">
      <span class="brand-square" aria-hidden="true"></span>
      <span class="brand-name">FERNCLIFF ADVISORY</span>
    </div>

    <div class="divider"></div>
    <h1 class="holder-name">Daniel Whitcombe</h1>

    <div class="address">
      <span class="icon-box" aria-hidden="true">
        <svg width="14" height="16" viewBox="0 0 14 16"><path d="M7 1a5 5 0 0 0-5 5c0 3.6 5 9 5 9s5-5.4 5-9a5 5 0 0 0-5-5z" fill="#fff"/><circle cx="7" cy="6" r="2" fill="#0b0b9c"/></svg>
      </span>
      <p>2870 North 9th Avenue, Summit Floor,<br>Elm Ridge, Illinois 60531</p>
    </div>

    <ul class="contact-list">
      <li>
        <span class="icon-box" aria-hidden="true">
          <svg width="14" height="10" viewBox="0 0 14 10"><rect x=".75" y=".75" width="12.5" height="8.5" fill="none" stroke="#fff" stroke-width="1.5"/><path d="M1 1l6 4.5L13 1" fill="none" stroke="#fff" stroke-width="1.5"/></svg>
        </span>
        dan@ferncliffadvisory.com
      </li>
      <li>
        <span class="icon-box" aria-hidden="true">
          <svg width="14" height="14" viewBox="0 0 14 14"><circle cx="7" cy="7" r="6" fill="none" stroke="#fff" stroke-width="1.4"/><path d="M1 7h12M7 1c-2.5 3-2.5 9 0 12M7 1c2.5 3 2.5 9 0 12" fill="none" stroke="#fff" stroke-width="1.1"/></svg>
        </span>
        www.ferncliffadvisory.com
      </li>
    </ul>

    <div class="band"></div>
  </section>

</main>
</body>
</html>
```